Yacht, Boats, Watersports company needs a redesign of business card

Hello Designers!
We are a Boat dealership company that sells fun in the water, we sell boats, Yachts, Kayaks and also yacht WaterSport toys. We are looking to redesign our business cards in to something a little bit more sophisticated. in a way that we can make better use of our company colors. I'm attaching a zipped file containing the company 3 sets of company logo which one is an horizontal another one is a vertical and also a chromed 3d logo. Also is included two set of business cards that we use and also some designs that i think it's interesting. We use PMS 2026c Orange and PMS 7687C Blue. I would like to see at least two different options with the orange as accent and also using blue as an accent color. It's really important for the business cards to have a font option and size that is legible to most people. Our current website is wwww.coralpennant.com. Please visit if you want to have a better feeling of the Boat dealership
You can send Single sided or double side options. We are now using single sided but we may be open for a double side option if we really like the design.
Target Market(s)
Marine, boat sales, yacht sales, water toys sales/
Contact Information for Business Card
Name: Dale Whitcombe
Address: 212 North Fenwick Lane,
Marlow Cove, FL 33190
Phone: 954-731-8842
Fax: 954:731-8843
Cell: 954-382-1490
Email: dw@coralpennant.com
Website: coralpennant.com
Requirements
Must have
- the current information of the business card provided.
logo
use the PMS Colors
Nice to have
- a touch of elegance and sophistication but simple
Should not have
- should not have any typography that is hard to read, the card should be simple but yet sophisticated.

```html
<!DOCTYPE html>
<html lang="en">
<head>
<meta charset="utf-8">
<title>Coral Pennant — Business Card</title>
<link href="https://fonts.googleapis.com/css2?family=Questrial&family=Mulish:wght@700&display=swap" rel="stylesheet">
<style>
  :root {
    --brand-blue: #1e3d6b;
    --brand-orange: #d95b29;
    --card-white: #ffffff;
    --stage: #d95b29;
  }
  * { margin: 0; padding: 0; box-sizing: border-box; }
  html, body {
    width: 1200px;
    height: 900px;
    overflow: hidden;
    background: var(--stage);
  }
  .business-card {
    position: absolute;
    left: 80px;
    top: 121px;
    width: 1040px;
    height: 657px;
    background: var(--card-white);
    overflow: hidden;
  }
  .color-panel {
    position: absolute;
    left: 0;
    top: 0;
    width: 384px;
    height: 100%;
    background: var(--brand-blue);
  }
  .brand-lockup {
    position: absolute;
    left: 461px;
    top: 68px;
    display: flex;
    align-items: center;
    gap: 16px;
  }
  .brand-dot {
    width: 74px;
    height: 74px;
    border-radius: 50%;
    background: var(--brand-orange);
  }
  .brand-name {
    font-family: "Questrial", sans-serif;
    font-size: 21px;
    letter-spacing: 0.08em;
    text-transform: uppercase;
    color: var(--brand-blue);
  }
  .person-name {
    position: absolute;
    left: 461px;
    top: 222px;
    font-family: "Mulish", sans-serif;
    font-weight: 700;
    font-size: 56px;
    line-height: 1;
    color: var(--brand-blue);
    letter-spacing: -0.005em;
    white-space: nowrap;
  }
  .contact-block {
    position: absolute;
    left: 461px;
    font-family: "Questrial", sans-serif;
    font-size: 26px;
    line-height: 30px;
    letter-spacing: 0.07em;
    color: var(--brand-blue);
    font-style: normal;
    white-space: nowrap;
  }
  .address { top: 355px; }
  .contact-lines { top: 430px; list-style: none; }
</style>
</head>
<body>
  <section class="business-card">
    <div class="color-panel"></div>

    <div class="brand-lockup">
      <span class="brand-dot"></span>
      <span class="brand-name">Coral Pennant</span>
    </div>

    <h1 class="person-name">Dale Whitcombe</h1>

    <address class="contact-block address">
      212 North Fenwick Lane, Marlow<br>
      Cove, FL 33190
    </address>

    <ul class="contact-block contact-lines">
      <li>TEL: 954-731-8842</li>
      <li>FAX: 954:731-8843</li>
      <li>Cell: 954-382-1490</li>
      <li>Email: dw@coralpennant.com</li>
      <li>URL: coralpennant.com</li>
    </ul>
  </section>
</body>
</html>
```